Life Coaching business needs a new flyer

We are an Australian business that specialises in Life Coaching, Career Coaching, Health and Wellness Coaching, Yoga and Pilates. We need a A4 double sided flyer that is full colour and folded to DL format. I have attached a couple of designs that I like and some pictures and would like the flyer to be bright yet stylish.

Industry/Entity Type

Life Coaching

```html
<!DOCTYPE html>
<html lang="en">
<head>
<meta charset="utf-8">
<title>Bright Path Coaching – DL Flyer</title>
<link rel="stylesheet" href="https://fonts.googleapis.com/css2?family=PT+Sans:ital,wght@0,400;0,700;1,400&family=EB+Garamond:wght@500;600&family=Cinzel:wght@500&family=Great+Vibes&display=swap">
<style>
  :root {
    --backdrop: #a9a9a9;
    --panel-blue: #3a6db1;
    --brand-green: #4db615;
    --green-light: #6cc23a;
    --teal: #1c8cc6;
    --corner-blue: #1766c0;
    --cover-sky: #dcecf5;
    --ink: #222;
    --muted: #555;
    --white: #fff;
  }
  * { box-sizing: border-box; margin: 0; padding: 0; }
  html, body { width: 874px; height: 1200px; overflow: hidden; }
  body {
    background: linear-gradient(180deg, #b3b3b3, var(--backdrop));
    font-family: "PT Sans", sans-serif;
    position: relative;
  }
  .sheet {
    position: absolute; left: 69px; width: 705px; height: 499px;
    overflow: hidden; background: var(--white);
    box-shadow: 0 2px 6px rgba(0,0,0,.25);
  }
  .sheet-outside { top: 75px; }
  .sheet-inside { top: 626px; }
  .shape-layer { position: absolute; inset: 0; }
  .abs { position: absolute; }

  /* outside – testimonials */
  .testimonials {
    left: 0; top: 0; width: 235px; height: 499px;
    background: var(--panel-blue); color: var(--white);
  }
  .testimonials h2 {
    position: absolute; left: 26px; top: 19px;
    font-family: "EB Garamond", serif; font-weight: 600; font-size: 14.5px;
  }
  .testimonials .quotes {
    position: absolute; left: 26px; top: 44px; width: 178px;
    font-size: 7.7px; line-height: 9.7px; text-align: justify;
  }
  .testimonials .quotes p { margin-bottom: 9.5px; }
  .photo-friends {
    position: absolute; left: 0; top: 340px; width: 235px; height: 159px;
    background: linear-gradient(180deg, #3f7cc6 0%, #5e9ad8 55%, #d98a6c 80%, #c8463f 100%);
  }

  /* outside – contact */
  .contact {
    left: 235px; top: 0; width: 235px; height: 499px;
    background: var(--brand-green); color: var(--white); text-align: center;
  }
  .contact .intro {
    position: absolute; left: 27px; top: 27px; width: 178px;
    font-size: 7.6px; line-height: 9.6px; text-align: left;
  }
  .contact .intro p + p { margin-top: 9px; }
  .contact .mark {
    position: absolute; left: 80px; top: 104px; width: 74px; height: 74px;
    border: 5px solid var(--white); border-radius: 50%;
  }
  .contact h3 {
    position: absolute; left: 0; right: 0; top: 181px;
    font-family: "EB Garamond", serif; font-weight: 600; font-size: 15px; line-height: 18px;
  }
  .contact .lines { position: absolute; left: 0; right: 0; top: 204px; font-size: 9.5px; }
  .contact .lines svg { display: block; margin: 0 auto 2px; }
  .contact .lines span { display: block; margin-bottom: 5px; }
  .offer {
    position: absolute; left: 0; top: 298px; width: 235px; height: 50px;
    background: var(--green-light);
    font-family: "EB Garamond", serif; font-weight: 600; font-size: 11px; line-height: 13.6px;
    padding-top: 5px;
  }
  .photo-coaches {
    position: absolute; left: 0; top: 348px; width: 235px; height: 151px;
    background: linear-gradient(180deg, #3f6a2c 0%, #26331f 60%, #3b3f44 100%);
  }

  /* outside – cover */
  .cover {
    left: 470px; top: 0; width: 235px; height: 499px;
    background: linear-gradient(180deg, var(--cover-sky) 0%, #cfe4f0 55%, #d9d5c8 88%, #c8c3b4 100%);
  }
  .cover .brand { position: absolute; left: 0; right: 0; top: 45px; text-align: center; }
  .cover .brand .dot {
    display: block; width: 54px; height: 54px; margin: 0 auto 10px;
    border: 4px solid var(--brand-green); border-radius: 50%;
  }
  .cover .brand .name {
    font-family: "Cinzel", serif; font-weight: 500; font-size: 16px;
    color: var(--teal); letter-spacing: .5px;
  }
  .cover .script {
    position: absolute; left: 0; right: 0; top: 158px; text-align: center;
    font-family: "Great Vibes", cursive; font-size: 28px; line-height: 30px;
    color: var(--teal);
  }

  /* inside */
  .col { position: absolute; top: 16px; font-size: 8.6px; line-height: 10.2px; color: var(--muted); }
  .col h2 {
    font-family: "EB Garamond", serif; font-weight: 600; font-size: 14px; line-height: 17px;
    color: var(--teal);
  }
  .col p { margin-bottom: 12px; }
  .col-intro { left: 26px; width: 178px; }
  .col-intro .question { color: var(--ink); font-weight: 700; font-size: 8.9px; line-height: 11px; margin-bottom: 7px; }
  .col-intro .answer { color: var(--ink); font-weight: 700; font-size: 8.9px; margin-bottom: 14px; }
  .col-intro h2 { margin-bottom: 8px; }
  .col-services { left: 258px; width: 177px; text-align: justify; }
  .col-services p { margin-bottom: 6px; }
  .col-services h2 { text-align: left; }
  .col-help { left: 496px; width: 185px; }
  .col-help h2 { margin-bottom: 3px; }
  .col-help .lead { margin-bottom: 10px; padding-left: 2px; }
  .help-list { list-style: none; margin-bottom: 14px; }
  .help-list li {
    font-style: italic; position: relative; padding-left: 15px; margin-bottom: 1.4px;
  }
  .help-list li svg { position: absolute; left: 0; top: 1px; }

  .photo-strip { position: absolute; top: 365px; height: 134px; width: 235px; }
  .photo-pool { left: 0; background: linear-gradient(135deg, #2aa9b5, #7fd4cc 50%, #1f8ea2); }
  .photo-smile { left: 235px; background: linear-gradient(135deg, #e9ecee, #d9b19c 55%, #e68aa4); }
  .photo-family { left: 470px; background: linear-gradient(135deg, #8bb03a, #e3a25a 55%, #c6763c); }
</style>
</head>
<body>

<section class="sheet sheet-outside">
  <div class="abs testimonials">
    <h2>Happy Clients Testimonials</h2>
    <div class="quotes">
      <p>“I have lost 10 kilos and now have the energy to play with my kids. Thanks Jenna for you support/guidance and helping me get rid of my limiting beliefs. I feel I can achieve anything now! The sky’s the limit” Maree, Mosman</p>
      <p>“I had always wanted to start up own café however every time it came to putting it into practice I would procrastinate and not achieve anything. I became overwhelmed with the whole process and never achieved anything. Jenna put it into bite sized chunks and helped me to set small achievable goals. I am now a happy café owner.” Tess, Double Bay</p>
      <p>“Jenna has helped to change my life around in all aspects. I would have been lost without her. Thanks Jenna for your professionalism, support and guidance.” Carla, Cremorne</p>
      <p>“I was so busy with kids, work, and my husband I lost who I was. Jenna has helped me find the person I am again.” Helen, Chatswood</p>
      <p>“When I started with Coach Jenna, I didn’t know anything about coaching. I called her because she helped a friend of mine make a career change that was a perfect fit for her. I had the opportunity to make a change too and did not know where to start. I am now in a job that I love. I would recommend Jenna to everyone.” Daniel, Texas America</p>
    </div>
    <div class="photo-friends" role="img" aria-label="Photo of four happy friends jumping with arms raised against a blue sky"></div>
  </div>

  <div class="abs contact">
    <div class="intro">
      <p>Bright Path Coaching and Meditation Studio is a professional service that can help you achieve the goals that you are looking for in Life Coaching, Meditation, and Yoga/Pilates.</p>
      <p>If you are ready to take your life to the next level and would like to know more, please</p>
    </div>
    <span class="mark" aria-hidden="true"></span>
    <h3>contact us.</h3>
    <div class="lines">
      <svg width="12" height="10" viewBox="0 0 12 10" aria-hidden="true"><path d="M1 3 Q6 -1 11 3 L9 4 L8 2.5 H4 L3 4 Z M3 5 H9 L10 9 H2 Z" fill="#fff"/></svg>
      <span>02 9000 4127</span>
      <svg width="12" height="9" viewBox="0 0 12 9" aria-hidden="true"><rect x="0.5" y="0.5" width="11" height="8" fill="none" stroke="#fff"/><path d="M0.5 0.5 L6 5 L11.5 0.5" fill="none" stroke="#fff"/></svg>
      <span>hello@brightpathcoaching.com.au</span>
      <svg width="11" height="11" viewBox="0 0 11 11" aria-hidden="true"><circle cx="5.5" cy="5.5" r="5" fill="none" stroke="#fff"/><ellipse cx="5.5" cy="5.5" rx="2.2" ry="5" fill="none" stroke="#fff"/><path d="M0.5 5.5 H10.5" stroke="#fff"/></svg>
      <span>brightpathcoaching.com.au</span>
    </div>
    <div class="offer">Free Introductory Life Coaching<br>Phone/Video session - 20 mins<br>(To see if coaching is right for you)</div>
    <div class="photo-coaches" role="img" aria-label="Portrait photo of the two coaches, a woman and a man"></div>
  </div>

  <div class="abs cover" role="img" aria-label="Photo of a couple in yoga tree pose on a misty beach">
    <div class="brand">
      <span class="dot" aria-hidden="true"></span>
      <span class="name">Bright Path</span>
    </div>
    <div class="script">Life Coaching<br>Meditation<br>Yoga/Pilates</div>
  </div>

  <svg class="shape-layer" width="705" height="499" viewBox="0 0 705 499" aria-hidden="true">
    <path d="M470 0 H600 C520 12 470 90 470 275 Z" fill="var(--brand-green)"/>
    <path d="M705 245 C702 370 665 460 600 499 H705 Z" fill="var(--corner-blue)"/>
  </svg>
</section>

<section class="sheet sheet-inside">
  <svg class="shape-layer" width="705" height="499" viewBox="0 0 705 499" aria-hidden="true">
    <path d="M0 0 H60 C30 6 8 28 0 58 Z" fill="var(--brand-green)"/>
    <path d="M705 268 V365 H630 C672 355 700 320 705 268 Z" fill="var(--corner-blue)"/>
  </svg>

  <div class="col col-intro">
    <p class="question">Are you looking at making changes this year?</p>
    <p class="question">Are you stuck in a rut or at a crossroad in your life?</p>
    <p class="question">Are you wanting to lose weigh but can’t get motivated?</p>
    <p class="question" style="margin-top:12px">Do you have ongoing problems with your career, relationships, or just life itself?</p>
    <p class="answer">Life coaching is the answer</p>
    <h2>Bright Path Coaching and Meditation Studio</h2>
    <p>Our mission is to help you become the best possible person you can be. Mentally, physically, and spiritually.</p>
    <p style="margin-top:14px">We offer highly qualified and compassionate trainers/coaches for Life Coaching, Meditation, Yoga and Pilates.</p>
    <p style="margin-top:14px">They will guide and motivate you every step of the way to achieve all your dreams and goals.</p>
    <p style="margin-top:14px">They will make you be the best you can be</p>
  </div>

  <div class="col col-services">
    <h2>Life Coaching</h2>
    <p>Your Life Coach will give you the confidence and the ability to move forward in a positive manner in all areas of your life where you crave change.</p>
    <p style="margin-top:12px">Life Coaching is about breaking down the barriers preventing this change from happening, and creating the ideal environment for positive action to take place. It is a holistic approach, which looks at the present and sets goals for a totally successful future.</p>
    <h2>Career Coaching</h2>
    <p>Are you at a crossroads in your career and at a loss about what to do next? Do you want your work to be in alignment with the authentic you? It can be difficult to assess career options, goals, and strategies, and have the confidence to implement changes on your own. With the right coaching support, you will gain the clarity that you need to take control and have a fulfilling and rewarding career.</p>
    <h2>Wellness Coaching</h2>
    <p>Health and wellness coaches help their clients find the motivation and tools to achieve their health and wellness goals, working with the client to examine and improve the psychological framework that supports those goals.</p>
  </div>

  <div class="col col-help">
    <h2>Why Would I Need Help?</h2>
    <p class="lead">Coaching is for anyone who wants to make lasting changes in their life.<br>Coaching can assist with such issues as:</p>
    <ul class="help-list">
      <li><svg width="10" height="8" viewBox="0 0 10 8"><ellipse cx="5" cy="4" rx="4.5" ry="3.5" fill="none" stroke="var(--brand-green)" stroke-width="1.4"/><circle cx="5" cy="4" r="1.4" fill="var(--teal)"/></svg>Creating a better work- life balance</li>
      <li><svg width="10" height="8" viewBox="0 0 10 8"><ellipse cx="5" cy="4" rx="4.5" ry="3.5" fill="none" stroke="var(--brand-green)" stroke-width="1.4"/><circle cx="5" cy="4" r="1.4" fill="var(--teal)"/></svg>Resolving relationship issues</li>
      <li><svg width="10" height="8" viewBox="0 0 10 8"><ellipse cx="5" cy="4" rx="4.5" ry="3.5" fill="none" stroke="var(--brand-green)" stroke-width="1.4"/><circle cx="5" cy="4" r="1.4" fill="var(--teal)"/></svg>Career guidance</li>
      <li><svg width="10" height="8" viewBox="0 0 10 8"><ellipse cx="5" cy="4" rx="4.5" ry="3.5" fill="none" stroke="var(--brand-green)" stroke-width="1.4"/><circle cx="5" cy="4" r="1.4" fill="var(--teal)"/></svg>Stress management</li>
      <li><svg width="10" height="8" viewBox="0 0 10 8"><ellipse cx="5" cy="4" rx="4.5" ry="3.5" fill="none" stroke="var(--brand-green)" stroke-width="1.4"/><circle cx="5" cy="4" r="1.4" fill="var(--teal)"/></svg>Weight loss and fitness</li>
      <li><svg width="10" height="8" viewBox="0 0 10 8"><ellipse cx="5" cy="4" rx="4.5" ry="3.5" fill="none" stroke="var(--brand-green)" stroke-width="1.4"/><circle cx="5" cy="4" r="1.4" fill="var(--teal)"/></svg>Motivation and goal setting</li>
      <li><svg width="10" height="8" viewBox="0 0 10 8"><ellipse cx="5" cy="4" rx="4.5" ry="3.5" fill="none" stroke="var(--brand-green)" stroke-width="1.4"/><circle cx="5" cy="4" r="1.4" fill="var(--teal)"/></svg>Boosting your self esteem</li>
      <li><svg width="10" height="8" viewBox="0 0 10 8"><ellipse cx="5" cy="4" rx="4.5" ry="3.5" fill="none" stroke="var(--brand-green)" stroke-width="1.4"/><circle cx="5" cy="4" r="1.4" fill="var(--teal)"/></svg>Overcoming negative emotions and thoughts</li>
      <li><svg width="10" height="8" viewBox="0 0 10 8"><ellipse cx="5" cy="4" rx="4.5" ry="3.5" fill="none" stroke="var(--brand-green)" stroke-width="1.4"/><circle cx="5" cy="4" r="1.4" fill="var(--teal)"/></svg>Better time management</li>
    </ul>
    <h2>Meditation</h2>
    <p>We specialise in teaching meditation from beginners to advanced and teach a variety of techniques for stress reduction, peace of mind, stillness, and clarity.</p>
    <h2>Yoga/Pilates</h2>
    <p>Your highly qualified and experienced Yoga or Pilates instructor will come to you and create a fun and varied workout based on what you enjoy and what your goals are.</p>
  </div>

  <div class="photo-strip photo-pool" role="img" aria-label="Photo of a woman in a sun hat relaxing on a pink float in clear turquoise water"></div>
  <div class="photo-strip photo-smile" role="img" aria-label="Photo of a smiling grey-haired man in a pink shirt"></div>
  <div class="photo-strip photo-family" role="img" aria-label="Photo of a mother hugging her young daughter outdoors in warm sunlight"></div>
</section>

</body>
</html>
```